Brindle Sky Port needs a new upscale business card design for our high end aircraft hangar complex

Brindle Sky Port (BSP) is a large, upscale jet hangar complex in the US housing expensive aircraft. We need a new business card design, using our current logo. We will be attending a industry convention and need a card design that will stand out and be remembered by aircraft owners and private pilots.

Target Market(s)

Aircraft pilots or owners looking for a new upscale hangar

Industry/Entity Type

Airport

Contact Information for Business Card

I like to use very heavy card stock, 400#, double sided. Square, no rounded edges please.

Colors
3276b5
0255a3
85abd2

Requirements
Must have
• An expensive, classy design, vivid colors.
Nice to have
• Needs to look very expensive and classy, and have some "pop". Designer must be able to download or copy my current typeface or fonts.
• One card side might be black with the "Logo and Brindle Sky Port Double line image in blue (or try gold, or glossy black), and perhaps have a grayed out "K720 jet silhouette". The other card side would have our contact info, and perhaps the "BSP Logo only". I'd like my contact info 'stacked', not in a paragraph format.
Should not have
• Should not look "too busy". Having a double-sided card will help.

```html
<!DOCTYPE html>
<html lang="en">
<head>
<meta charset="utf-8">
<title>Brindle Sky Port – Business Card</title>
<link rel="stylesheet" href="https://fonts.googleapis.com/css2?family=Open+Sans:wght@400&family=Titillium+Web:wght@600;700&display=swap">
<style>
  :root {
    --backdrop: #8e8f90;
    --card-black: #0f0f10;
    --blue-deep: #0a2f55;
    --blue-mid: #1d5488;
    --blue-bright: #2a6aa6;
    --logo-blue: #2f69a8;
    --ink-dark: #0c0d0f;
    --text-light: #e6e8ea;
    --text-muted: #1a1a1a;
  }
  * { box-sizing: border-box; margin: 0; padding: 0; }
  html, body { width: 1105px; height: 1200px; overflow: hidden; }
  body {
    background: var(--backdrop);
    font-family: "Open Sans", sans-serif;
    position: relative;
  }
  .card {
    position: absolute;
    left: 180px;
    width: 746px;
    height: 425px;
    overflow: hidden;
  }
  .card-front { top: 120px; background: var(--card-black); }
  .card-back {
    top: 640px;
    background: radial-gradient(ellipse 60% 70% at 45% 40%, var(--blue-bright) 0%, var(--blue-mid) 45%, var(--blue-deep) 100%);
  }
  .header-band { position: absolute; left: 0; top: 0; width: 746px; height: 124px; }
  .holder { position: absolute; left: 47px; top: 34px; }
  .holder-name {
    font-family: "Titillium Web", sans-serif;
    font-weight: 700;
    font-size: 28px;
    letter-spacing: 0.5px;
    color: var(--ink-dark);
    line-height: 1;
  }
  .holder-title { font-size: 17px; color: var(--text-muted); margin-top: 4px; }
  .address {
    position: absolute; left: 46px; top: 166px;
    color: var(--text-light); font-size: 19px; line-height: 28px;
  }
  .address .web { letter-spacing: 3px; }
  .contacts {
    position: absolute; left: 46px; top: 270px;
    list-style: none; color: var(--text-light); font-size: 19px; line-height: 28px;
  }
  .contacts li { display: flex; align-items: center; gap: 14px; }
  .contacts svg { width: 18px; height: 18px; fill: var(--logo-blue); flex: none; }
  .brand-front {
    position: absolute; left: 470px; top: 215px; width: 240px;
    text-align: center; color: var(--logo-blue);
    font-family: "Titillium Web", sans-serif; font-weight: 700;
  }
  .brand-front .initials { font-size: 92px; line-height: 1; letter-spacing: 2px; }
  .brand-front .wordmark { font-size: 30px; line-height: 1.1; letter-spacing: 1px; }
  .brand-back {
    position: absolute; left: 0; top: 150px; width: 100%;
    text-align: center; color: var(--ink-dark);
    font-family: "Titillium Web", sans-serif; font-weight: 700;
    font-size: 120px; line-height: 1; letter-spacing: 4px;
  }
  .web-back {
    position: absolute; left: 0; top: 358px; width: 100%;
    text-align: center; color: var(--ink-dark);
    font-size: 21px; letter-spacing: 7px; font-weight: 400;
  }
</style>
</head>
<body>
  <section class="card card-front">
    <svg class="header-band" viewBox="0 0 746 124" preserveAspectRatio="none" aria-hidden="true">
      <defs>
        <radialGradient id="bandGlow" cx="0.4" cy="0.2" r="0.7">
          <stop offset="0" stop-color="#2a5f94"/>
          <stop offset="1" stop-color="#133a63"/>
        </radialGradient>
      </defs>
      <path d="M0 0 H746 V0 C640 30 560 112 400 123 L0 124 Z" fill="url(#bandGlow)"/>
    </svg>
    <div class="holder">
      <div class="holder-name">DANA WHITLOCK</div>
      <div class="holder-title">CEO/Founder</div>
    </div>
    <div class="address">
      <div>2140 Larkspur Road</div>
      <div>Anchorage, Alaska 99517</div>
      <div class="web">www.skyportsite.com</div>
    </div>
    <ul class="contacts">
      <li><svg viewBox="0 0 24 24"><path d="M6.6 10.8a15.5 15.5 0 0 0 6.6 6.6l2.2-2.2c.3-.3.7-.4 1-.2 1.1.4 2.3.6 3.6.6.6 0 1 .4 1 1V20c0 .6-.4 1-1 1A17 17 0 0 1 3 4c0-.6.4-1 1-1h3.5c.6 0 1 .4 1 1 0 1.3.2 2.5.6 3.6.1.3 0 .7-.2 1z"/></svg>555 214 7730</li>
      <li><svg viewBox="0 0 24 24"><path d="M7 1h10a2 2 0 0 1 2 2v18a2 2 0 0 1-2 2H7a2 2 0 0 1-2-2V3a2 2 0 0 1 2-2zm0 3v14h10V4zm5 15.5a1 1 0 1 0 0 2 1 1 0 0 0 0-2z"/></svg>555 382 6195</li>
      <li><svg viewBox="0 0 24 24"><path d="M6 2h12v6H6zM3 9h18a1 1 0 0 1 1 1v8h-4v4H6v-4H2v-8a1 1 0 0 1 1-1zm5 7v4h8v-4z"/></svg>555 709 4418</li>
      <li><svg viewBox="0 0 24 24"><path d="M2 5h20v14H2zm2 2v.5l8 5 8-5V7z"/></svg>dana@skyportsite.com</li>
    </ul>
    <div class="brand-front">
      <div class="initials">BSP</div>
      <div class="wordmark">BRINDLE SKY PORT</div>
    </div>
  </section>

  <section class="card card-back">
    <div class="brand-back">BSP</div>
    <div class="web-back">www.skyportsite.com</div>
  </section>
</body>
</html>
```